Label design for our new range of organic honey.

We need a design for honey jars and tubs. The label needs to indicate we are located in the Western Australia. The design needs to be elegant, modern and attracting high end customers that focus on quality.

Need extra days to review

```html
<!DOCTYPE html>
<html lang="en">
<head>
<meta charset="utf-8">
<title>Organic Honey Label</title>
<link rel="stylesheet" href="https://fonts.googleapis.com/css2?family=Young+Serif&family=Lora:ital,wght@1,400&display=swap">
<style>
  :root {
    --backdrop: #ebebeb;
    --label-dark: #3b3b3c;
    --label-mid: #4a4a4b;
    --label-light: #5f5f60;
    --gold-deep: #9c8448;
    --gold: #c8b27a;
    --gold-light: #f1e6c4;
    --ink-light: #ffffff;
  }
  html, body {
    margin: 0;
    padding: 0;
    width: 1200px;
    height: 1200px;
    overflow: hidden;
    background: var(--backdrop);
  }
  .canvas {
    position: relative;
    width: 1200px;
    height: 1200px;
  }
  .label {
    position: absolute;
    inset: 0;
    width: 1200px;
    height: 1200px;
  }
  .serif { font-family: "Young Serif", Georgia, serif; }
  .italic { font-family: "Lora", Georgia, serif; font-style: italic; }
</style>
</head>
<body>
<main class="canvas">
  <svg class="label" viewBox="0 0 1200 1200" xmlns="http://www.w3.org/2000/svg">
    <defs>
      <linearGradient id="label-fill" x1="0" y1="0" x2="1" y2="0">
        <stop offset="0" stop-color="var(--label-light)"/>
        <stop offset="0.35" stop-color="var(--label-dark)"/>
        <stop offset="0.75" stop-color="var(--label-mid)"/>
        <stop offset="1" stop-color="var(--label-light)"/>
      </linearGradient>
      <linearGradient id="gold-foil" x1="0" y1="0" x2="1" y2="0">
        <stop offset="0" stop-color="var(--gold-deep)"/>
        <stop offset="0.4" stop-color="var(--gold-light)"/>
        <stop offset="0.7" stop-color="var(--gold)"/>
        <stop offset="1" stop-color="var(--gold-light)"/>
      </linearGradient>
    </defs>

    <!-- label band and hexagon badge -->
    <g class="label-shape" fill="url(#label-fill)">
      <rect class="label-band" x="100" y="267" width="1000" height="663"/>
      <polygon class="label-hexagon" points="322,197 878,197 1058,600 878,1003 322,1003 142,600"
               stroke="url(#label-fill)" stroke-width="24" stroke-linejoin="round"/>
    </g>

    <!-- gold hexagon frame -->
    <polygon class="hexagon-frame" points="350,228 850,228 1025,600 850,972 350,972 175,600"
             fill="none" stroke="url(#gold-foil)" stroke-width="3.5" stroke-linejoin="round"/>

    <!-- region map -->
    <rect class="region-map" role="img" aria-label="Outline map of Australia"
          x="250" y="320" width="740" height="580" rx="40"
          fill="#ffffff" fill-opacity="0.035"/>

    <!-- brand name -->
    <g class="brand-name">
      <circle cx="272" cy="643" r="8" fill="var(--gold)"/>
      <text class="serif" x="290" y="640" font-size="17" letter-spacing="2" fill="var(--ink-light)">
        <tspan x="290" y="640">SALTBUSH GROVE</tspan>
        <tspan x="290" y="664">HONEY</tspan>
      </text>
    </g>

    <!-- product titles -->
    <text class="serif product-descriptor" x="739" y="566" font-size="50" text-anchor="middle" fill="var(--ink-light)">organic</text>
    <text class="serif product-name" x="725" y="672" font-size="112" text-anchor="middle" fill="url(#gold-foil)">HONEY</text>
    <text class="serif product-purity" x="742" y="722" font-size="33" text-anchor="middle" fill="var(--ink-light)">100% Pure</text>

    <!-- origin -->
    <text class="italic origin" font-size="29" fill="var(--ink-light)">
      <tspan x="527" y="840" text-anchor="middle">from</tspan>
      <tspan x="576" y="872" text-anchor="middle">Western Australia</tspan>
    </text>
    <rect class="origin-rule" x="437" y="895" width="276" height="13" fill="url(#gold-foil)"/>
  </svg>
</main>
</body>
</html>
```